SitePress Direct-Booking Website for Bend, Oregon Vacation Rental — $750 Budget
Project Overview

We are looking for a talented SitePress designer/developer to create a clean, professional and inviting direct-booking website for Birch Lantern Retreat, an established short-term vacation rental in Bend, Oregon.

The property is currently successfully listed on Staynest and Hoplo. Our Staynest property has approximately a 4.98-star rating with more than 200 reviews, is an Staynest Visitor Pick, and ranks among the Top 1% of eligible homes.

Project Budget: $750

We will select the designer based on the quality of the initial concept, understanding of the property, proposed booking solution and ability to deliver a completed and functioning SitePress website.

Existing Staynest Listing

Please use our current Staynest listing as the primary reference for photographs, property details, amenities and design inspiration:

https://www.staynest-example.net/rooms/48172036

Original high-resolution photographs and additional property information will be provided to the selected designer.

Design Direction

We want the website to feel:

Upscale but comfortable
Warm and welcoming
Clean and uncluttered
Pacific Northwest / Central Oregon
Professional rather than corporate
Highly visual with large property photographs
Easy to navigate
Excellent on phones, tablets and desktop computers

We welcome creativity and want designers to show us their vision for the property rather than simply copying our Staynest listing.

The website should immediately communicate that Birch Lantern Retreat is a highly rated vacation rental in an excellent Bend location.

Key Property Features
3 bedrooms
2 bathrooms
Sleeps up to 6 guests
Pet friendly
Approximately a 5-minute walk to Bend's Tannery Row Quarter
Near restaurants, shopping and Larkspur Fields Pavilion
Private fenced backyard
Covered outdoor area
Off-street driveway parking
Fireplace
Well-equipped kitchen
Staynest Prime Keeper
Staynest Visitor Pick
Top 1% of eligible Staynest homes
Approximately 4.98 stars with 200+ guest reviews

Our location, guest reviews, cleanliness, comfort, backyard, pet-friendly accommodations and walkability should be major selling points throughout the website.

Website Structure

We anticipate approximately 6–7 pages:

Home

Large hero photograph with a strong opening message and prominent BOOK DIRECT and CHECK AVAILABILITY buttons.

The home page should quickly communicate:

BIRCH LANTERN RETREAT — BEND, OREGON

3 Bedrooms | 2 Baths | Sleeps 6 | Pet Friendly | Walk to Tannery Row

Our exceptional guest rating and Staynest history should also be prominently featured.

The House

Bedrooms, bathrooms, kitchen, living areas, backyard and major amenities.

Photo Gallery

Large, attractive and fast-loading photographs with an easy-to-use mobile gallery.

Location / Explore Bend

Tannery Row Quarter, Larkspur Fields Pavilion, Deschutes River, restaurants, breweries, shopping, downtown Bend and nearby outdoor recreation.

Guest Reviews

Selected guest reviews and prominent presentation of our strong Staynest reputation.

Availability & Book Direct

A simple and professional direct-booking experience.

Contact / FAQ

Contact information plus common questions regarding pets, parking, check-in/check-out, cancellations and other policies.

IMPORTANT — Direct Booking & Credit Card Requirements

We want guests to be able to book directly through the website without having to contact us first.

The website should use a proven SitePress vacation-rental booking plugin or system rather than a custom-built reservation/payment system.

Guests should be able to:

Select arrival and departure dates
See available dates
Enter number of guests
See nightly charges
See cleaning fees
See applicable lodging taxes and other charges
See the complete reservation total before paying
Enter guest/contact information
Pay securely by credit or debit card
Receive an automatic reservation confirmation

Paywell is our preferred credit-card processor.

Credit-card information must be processed securely through Paywell or another established payment processor. Credit-card information should NOT be stored directly on our SitePress website.

Staynest & Hoplo Calendar Synchronization

This is very important.

The direct-booking calendar must synchronize with our existing Staynest and Hoplo calendars to reduce the possibility of double bookings.

For this single-property website, we prefer a simple solution using Staynest/Hoplo calendar or iCal synchronization rather than an expensive monthly channel-management service, if practical.

The designer should clearly identify the booking plugin/system they propose using.

IMPORTANT — Tell Us Your Proposed Booking Solution

As part of your submission, please tell us:

Which SitePress booking plugin/system you recommend.
Whether it synchronizes availability with Staynest and Hoplo.
Whether it integrates directly with Paywell.
The initial cost of the plugin/software.
Any annual or monthly fees.
Whether any additional paid software or services will be required.

We strongly prefer a solution with little or no ongoing monthly software expense.

We do not want to select a designer and later discover that the proposed booking system requires an expensive monthly subscription.

SitePress & Technical Requirements

The completed project should include:

Fully functioning SitePress website
Responsive desktop/tablet/mobile design
Fast-loading pages
Optimized photographs
SSL/HTTPS compatibility
Direct-booking functionality
Paywell payment integration
Staynest calendar synchronization
Hoplo calendar synchronization
Automatic booking confirmations
Cleaning fee and lodging-tax calculations
Contact form
Vizor Maps/location integration
Basic spam/security protection
Vizor Metrics capability
Basic SEO setup
Search-engine submission capability
Easy owner editing of text, rates and photographs
Search Engine Optimization

The website should be structured for Vizor and other search engines.

Important search themes include:

Bend Oregon vacation rental
Bend Oregon vacation home
Tannery Row Quarter vacation rental
Vacation rental near Tannery Row Bend
Bend Oregon pet-friendly vacation rental
Bend vacation rental near Larkspur Fields Pavilion
Bend Oregon direct booking vacation rental

We are not expecting an extensive ongoing SEO campaign for the $750 project. We do expect proper page titles, descriptions, headings, image optimization and a good technical foundation for future SEO.

Ownership

Upon completion and final payment:

We own the completed SitePress website.
We receive full SitePress administrator access.
We control the domain and hosting accounts.
We own all custom design files created for the project.
All necessary login credentials are provided to us.
The website can be moved to another SitePress hosting provider in the future.
There should be no proprietary dependency on the developer after completion.
What We Want From Contestants

Please review our Staynest listing before submitting your concept.

We are particularly interested in seeing an initial homepage concept showing how you would present:

Birch Lantern Retreat
The Bend / Tannery Row location
Our photography
Our exceptional guest reviews and ratings
The Book Direct message
The availability/booking call-to-action

We will provide feedback on the concepts we like and work with the selected designer to refine and complete the website.

Our Goal

Our objective is straightforward:

Create a beautiful, trustworthy and easy-to-use website that encourages guests to book Birch Lantern Retreat directly with us.

The website will complement—not replace—our existing Staynest and Hoplo listings.

We want repeat guests and new customers to have an easy way to find the property, check availability and book directly while receiving the same professional experience they expect from a major vacation-rental platform.

Target Market(s)

Consumers looking to to travel to Mexico for vacation. Family or couples

Industry/Entity Type

Short term vacation rental industry

Coding

Coded - Design and coding required

Number of Pages Required

5+ page

Requirements
Must have
• Capabilities to accept credit card payments and link to other rental property sites calendars such as HOPLO and Staynset
Nice to have
• Option for best plugins for property rental

```html
<!DOCTYPE html>
<html lang="en">
<head>
<meta charset="utf-8">
<title>Birch Lantern Retreat — Bend, Oregon</title>
<link href="https://fonts.googleapis.com/css2?family=Cormorant+Garamond:wght@500;600&family=Montserrat:wght@400;500;600;700&display=swap" rel="stylesheet">
<style>
:root{
  --green:#4b5e3a;
  --green-dark:#3e4f30;
  --ink:#2c2a24;
  --dark:#35342b;
  --cream:#f8f6f1;
  --white:#ffffff;
  --muted:#5a574f;
  --gold:#d99a2b;
  --line:#e4e0d6;
  --serif:'Cormorant Garamond', Georgia, serif;
  --sans:'Montserrat', Arial, sans-serif;
}
*{box-sizing:border-box;margin:0;padding:0}
html,body{width:1200px;height:2331px;overflow:hidden}
body{background:var(--cream);font-family:var(--sans);color:var(--ink);position:relative}
.abs{position:absolute}
.eyebrow{font-family:var(--sans);font-weight:600;font-size:10px;line-height:14px;letter-spacing:1.6px;color:var(--green);text-transform:uppercase}
.btn{display:flex;align-items:center;justify-content:center;font-family:var(--sans);font-weight:600;font-size:11px;letter-spacing:.8px;text-transform:uppercase;color:var(--white);background:var(--green);text-decoration:none}
.btn-outline{background:transparent;border:1.5px solid var(--white)}
.btn-white{background:var(--white);color:var(--green)}
.photo{border-radius:6px}

/* header */
.site-header{left:0;top:0;width:1200px;height:105px;background:var(--cream)}
.brand{left:63px;top:28px;display:flex;align-items:center;gap:10px}
.brand-mark{width:10px;height:10px;background:var(--green);border-radius:50%}
.brand-name{font-family:var(--serif);font-weight:600;font-size:19px;line-height:21px;letter-spacing:1.5px;color:var(--ink)}
.brand-sub{font-family:var(--sans);font-size:8px;letter-spacing:3px;color:var(--ink);margin-top:4px}
.main-nav{left:378px;top:44px;display:flex;gap:26px;font-size:10px;font-weight:600;letter-spacing:.3px}
.main-nav a{color:var(--ink);text-decoration:none}
.main-nav a.active{color:var(--green)}
.header-cta{left:1059px;top:33px;width:114px;height:37px;font-size:10px}

/* hero */
.hero{left:0;top:105px;width:1200px;height:483px;background:linear-gradient(90deg,#2e2419 0%,#5a4633 35%,#8a7560 55%,#b8b1a0 75%,#8ea27a 100%)}
.hero-shade{left:0;top:0;width:700px;height:483px;background:linear-gradient(90deg,rgba(20,15,10,.55),rgba(20,15,10,0))}
.hero-copy{left:69px;top:74px;color:var(--white)}
.hero-copy .eyebrow{color:var(--white);font-size:13px;letter-spacing:2.4px;font-weight:500}
.hero-title{font-family:var(--serif);font-weight:500;font-size:66px;line-height:68px;margin-top:18px;letter-spacing:.5px;white-space:nowrap}
.hero-place{font-size:15px;letter-spacing:4.5px;font-weight:500;margin-top:16px}
.hero-facts{font-size:12px;font-weight:600;letter-spacing:.6px;line-height:27px;margin-top:18px}
.hero-actions{display:flex;gap:11px;margin-top:32px}
.hero-actions .btn{width:181px;height:44px;font-size:11px}

/* trust bar */
.trust-bar{left:0;top:588px;width:1200px;height:62px;background:var(--dark);display:flex;align-items:center;justify-content:center;color:var(--white)}
.trust-item{display:flex;align-items:center;gap:11px;padding:0 48px;font-size:11px;font-weight:600;letter-spacing:.3px}
.trust-item small{display:block;font-weight:400;font-size:10px;color:#cfcac0;margin-top:3px}
.trust-sep{width:1px;height:30px;background:#6a685d}

/* location */
.location-copy{left:104px;top:684px;width:340px}
.section-title{font-family:var(--serif);font-weight:500;color:var(--ink)}
.location-copy h2{font-size:38px;line-height:41px;margin-top:10px}
.location-copy p{font-size:12px;line-height:20.5px;color:#3d3b35;margin-top:12px;width:350px}
.perks{left:80px;top:895px;display:flex}
.perk{width:112px;text-align:center;font-size:10px;line-height:19px;color:#4d4a43;white-space:nowrap}
.perk svg{display:block;margin:0 auto 8px}
.explore-btn{left:98px;top:998px;width:159px;height:36px;font-size:10px}
.location-photo{left:543px;top:680px;width:571px;height:354px;background:linear-gradient(180deg,#9fbcd8 0%,#c9d7e0 35%,#4e6a3f 55%,#7a5238 66%,#5f8aa0 80%,#3e5866 100%)}

/* house */
.house-head{left:0;top:1058px;width:1200px;text-align:center}
.house-head h2{font-size:33px;margin-top:10px}
.rooms{left:47px;top:1132px;display:flex;gap:10px}
.room{width:175px;text-align:center}
.room .photo{height:168px}
.room h3{font-family:var(--serif);font-weight:500;font-size:14px;margin-top:14px;color:var(--ink)}
.room p{font-size:10px;color:#55524a;margin-top:6px}
.house-btn{left:504px;top:1373px;width:175px;height:36px;font-size:10px}

/* book direct band */
.band{left:0;top:1440px;width:1200px;height:260px;background:linear-gradient(180deg,#e7b585 0%,#c9a07e 25%,#4c5a52 60%,#26332b 100%)}
.why-card{left:62px;top:1460px;width:780px;height:218px;background:var(--white);border-radius:8px;display:flex;align-items:flex-start;padding:32px 0 0 32px}
.why-intro{width:240px;height:156px;border-right:1px solid var(--line)}
.why-intro h2{font-size:34px;line-height:38px;margin-top:12px}
.why-list{display:flex;padding-left:6px}
.why{width:125px;text-align:center;padding:0 4px}
.why svg{display:block;margin:0 auto 12px}
.why h3{font-family:var(--serif);font-weight:600;font-size:14px;line-height:19px}
.why p{font-size:9.5px;line-height:17px;color:#55524a;margin-top:8px}
.avail-card{left:911px;top:1468px;width:220px;height:210px;background:var(--green);border-radius:6px;color:var(--white);padding:24px 24px}
.avail-head{display:flex;gap:12px;align-items:flex-start}
.avail-head h3{font-family:var(--serif);font-weight:500;font-size:18px;line-height:21px}
.avail-card p{font-size:11px;line-height:17.5px;margin-top:16px;color:#e9ece2}
.avail-card .btn{width:171px;height:37px;margin-top:16px;font-size:10px}

/* reviews */
.reviews-head{left:0;top:1719px;width:1200px;text-align:center}
.reviews-head h2{font-size:32px;margin-top:10px}
.review{top:1788px;width:266px;height:152px;background:var(--white);border:1px solid #efebe3;border-radius:6px;padding:20px 18px}
.stars{color:#d9712b;font-size:13px;letter-spacing:3px}
.review p{font-size:9.5px;line-height:17px;color:#3b3933;margin-top:8px}
.review .who{font-size:9.5px;font-weight:600;margin-top:12px}
.rating{left:960px;top:1792px;width:156px;text-align:center}
.rating .score{font-family:var(--serif);font-weight:600;font-size:38px;line-height:40px;margin-top:4px}
.rating .lbl{font-size:9px;color:#3b3933}
.rating ul{list-style:none;font-size:11px;line-height:20px;color:#3b3933;margin-top:24px}
.reviews-btn{left:505px;top:1952px;width:176px;height:27px;font-size:9.5px}

/* closing cta */
.cta{left:0;top:1987px;width:1200px;height:216px;background:linear-gradient(180deg,#5d6160 0%,#8d8a86 30%,#4a4a3e 60%,#3b4a4d 100%)}
.cta-copy{left:78px;top:2022px;color:var(--white)}
.cta-copy .eyebrow{color:var(--white);font-size:11px;letter-spacing:2px;font-weight:500}
.cta-copy h2{font-family:var(--serif);font-weight:500;font-size:37px;line-height:40px;margin-top:10px;color:var(--white)}
.cta-actions{display:flex;gap:20px;margin-top:18px}
.cta-actions .btn{width:189px;height:37px}

/* footer */
.site-footer{left:0;top:2203px;width:1200px;height:128px;background:var(--dark);color:#e9e6de}
.foot-brand{left:121px;top:22px;display:flex;align-items:center;gap:10px}
.foot-brand .brand-name{color:#f0ede5;font-size:16px;line-height:18px}
.foot-brand .brand-sub{color:#cfcac0;font-size:7px}
.foot-brand .brand-mark{background:#cfcac0}
.foot-col{top:16px;font-size:8px;line-height:14px}
.foot-col h4{font-size:8.5px;font-weight:600;letter-spacing:.8px;margin-bottom:6px}
.foot-col a{color:#d9d5cc;text-decoration:none;display:block}
.foot-links{display:flex;gap:42px}
.foot-contact div{display:flex;align-items:center;gap:6px}
.socials{display:flex;gap:12px}
.socials span{width:24px;height:24px;border:1.2px solid #e9e6de;border-radius:50%}
.foot-bottom{top:104px;font-size:8.5px;color:#cfcac0}
</style>
</head>
<body>

<header class="site-header abs">
  <div class="brand abs">
    <span class="brand-mark"></span>
    <div>
      <div class="brand-name">BIRCH LANTERN<br>RETREAT</div>
      <div class="brand-sub">BEND, OREGON</div>
    </div>
  </div>
  <nav class="main-nav abs">
    <a class="active" href="#">HOME</a><a href="#">THE HOUSE</a><a href="#">GALLERY</a><a href="#">EXPLORE BEND</a><a href="#">REVIEWS</a><a href="#">BOOK DIRECT</a><a href="#">CONTACT / FAQ</a>
  </nav>
  <a class="btn header-cta abs" href="#">BOOK DIRECT</a>
</header>

<section class="hero abs" role="img" aria-label="Living room with stone fireplace, sectional sofa and large windows onto a green backyard">
  <div class="hero-shade abs"></div>
  <div class="hero-copy abs">
    <div class="eyebrow">YOUR BEND GETAWAY</div>
    <h1 class="hero-title">BIRCH LANTERN<br>RETREAT</h1>
    <div class="hero-place">BEND, OREGON</div>
    <div class="hero-facts">3 BEDROOMS &nbsp;|&nbsp; 2 BATHS &nbsp;|&nbsp; SLEEPS 6 &nbsp;|&nbsp; PET FRIENDLY<br>WALK TO TANNERY ROW QUARTER</div>
    <div class="hero-actions">
      <a class="btn" href="#">CHECK AVAILABILITY</a>
      <a class="btn btn-outline" href="#">BOOK DIRECT</a>
    </div>
  </div>
</section>

<div class="trust-bar abs">
  <div class="trust-item">
    <svg width="20" height="20" viewBox="0 0 24 24"><path d="M12 2l3 6.5 7 .8-5.2 4.8 1.5 7L12 17.6 5.7 21l1.5-7L2 9.3l7-.8z" fill="var(--gold)"/></svg>
    <div>4.98 OUT OF 5 STARS<small>200+ Guest Reviews</small></div>
  </div>
  <span class="trust-sep"></span>
  <div class="trust-item">
    <svg width="24" height="24" viewBox="0 0 24 24"><circle cx="12" cy="12" r="9" fill="none" stroke="#e9e6de" stroke-width="1.5"/></svg>
    <div>STAYNEST VISITOR PICK</div>
  </div>
  <span class="trust-sep"></span>
  <div class="trust-item">
    <svg width="24" height="24" viewBox="0 0 24 24" fill="none" stroke="var(--gold)" stroke-width="1.8"><path d="M7 3h10v5a5 5 0 01-10 0z"/><path d="M7 5H3v2a4 4 0 004 4M17 5h4v2a4 4 0 01-4 4M12 13v4M8 21h8M9 17h6v4H9z"/></svg>
    <div>TOP 1%<small>Of Eligible Homes</small></div>
  </div>
  <span class="trust-sep"></span>
  <div class="trust-item">
    <svg width="22" height="24" viewBox="0 0 22 24" fill="none" stroke="#e9e6de" stroke-width="1.6"><path d="M11 2l8 3v6c0 6-4 9-8 11-4-2-8-5-8-11V5z"/><path d="M7 12l3 3 5-6"/></svg>
    <div>STAYNEST PRIME KEEPER</div>
  </div>
</div>

<section class="location-copy abs">
  <div class="eyebrow">THE PERFECT BEND LOCATION</div>
  <h2 class="section-title">Walk to the Best<br>of Bend</h2>
  <p>Just a 5-minute walk to the Tannery Row Quarter with restaurants, shopping, entertainment and the Deschutes River. Close to Larkspur Fields Pavilion, downtown Bend and endless outdoor adventures.</p>
</section>
<div class="perks abs">
  <div class="perk"><svg width="26" height="30" viewBox="0 0 26 30" fill="none" stroke="#4d4a43" stroke-width="1.6" stroke-linecap="round"><circle cx="14" cy="4" r="2.5"/><path d="M13 9l-3 8 5 4 1 7M10 17l-3 10M12 10l5 4 3-1M12 10l-5 3-1 4"/></svg>5-Min Walk to<br>Tannery Row Quarter</div>
  <div class="perk"><svg width="26" height="30" viewBox="0 0 26 30" fill="none" stroke="#4d4a43" stroke-width="1.6"><path d="M13 28s9-9 9-16a9 9 0 00-18 0c0 7 9 16 9 16z"/><circle cx="13" cy="12" r="3"/></svg>Near Restaurants<br>&amp; Shopping</div>
  <div class="perk"><svg width="26" height="30" viewBox="0 0 26 30" fill="none" stroke="#4d4a43" stroke-width="1.6"><path d="M9 23V6l12-3v17"/><circle cx="6" cy="23" r="3"/><circle cx="18" cy="20" r="3"/></svg>Larkspur Fields<br>Pavilion</div>
  <div class="perk"><svg width="32" height="30" viewBox="0 0 32 30" fill="none" stroke="#4d4a43" stroke-width="1.6" stroke-linejoin="round"><path d="M2 24l9-14 5 7 4-5 10 12z"/><path d="M9 13l2 2 2-2"/></svg>Adventure<br>All Around</div>
</div>
<a class="btn explore-btn abs" href="#">EXPLORE BEND</a>
<div class="location-photo photo abs" role="img" aria-label="Historic brick mill building among pine trees beside the rushing Deschutes River"></div>

<section class="house-head abs">
  <div class="eyebrow">THE HOUSE</div>
  <h2 class="section-title">Comfortable. Clean. Designed for Your Stay.</h2>
</section>
<div class="rooms abs">
  <div class="room"><div class="photo" role="img" aria-label="Bedroom with upholstered headboard and white bedding" style="background:linear-gradient(160deg,#d9d2c4,#8f8574 70%,#6b6a52)"></div><h3>Comfortable Bedrooms</h3><p>Sleeps up to 6 guests</p></div>
  <div class="room"><div class="photo" role="img" aria-label="Bright kitchen with island and bar stools" style="background:linear-gradient(160deg,#eeeae2,#c4b7a2 60%,#6e5a44)"></div><h3>Well-Equipped Kitchen</h3><p>Cook meals &amp; gather together</p></div>
  <div class="room"><div class="photo" role="img" aria-label="Living room with fireplace and sectional sofa" style="background:linear-gradient(160deg,#c9c2b4,#8b7a66 55%,#5c4b3a)"></div><h3>Cozy Living Room</h3><p>Relax by the fireplace</p></div>
  <div class="room"><div class="photo" role="img" aria-label="Fenced backyard with covered patio and string lights" style="background:linear-gradient(180deg,#2d2a22 0%,#5a4a34 45%,#3f7a2c 70%,#4f8a34)"></div><h3>Private Fenced Backyard</h3><p>Covered outdoor area</p></div>
  <div class="room"><div class="photo" role="img" aria-label="House front with garage and driveway" style="background:linear-gradient(180deg,#b8cde0 0%,#8a8f88 45%,#6f7168 70%,#5a5c58)"></div><h3>Off-Street Parking</h3><p>Private driveway</p></div>
  <div class="room"><div class="photo" role="img" aria-label="Pet dog sitting outdoors among pine trees" style="background:linear-gradient(160deg,#4c6a3a,#b99c7a 55%,#6a5a42)"></div><h3>Pet Friendly</h3><p>We welcome your pets</p></div>
</div>
<a class="btn house-btn abs" href="#">VIEW THE HOUSE</a>

<div class="band abs" role="img" aria-label="Sunset over snowy mountain and pine forest"></div>
<section class="why-card abs">
  <div class="why-intro">
    <div class="eyebrow">BOOK DIRECT &amp; SAVE</div>
    <h2 class="section-title">The Best Way<br>to Book</h2>
  </div>
  <div class="why-list">
    <div class="why"><svg width="34" height="36" viewBox="0 0 34 36" fill="none" stroke="var(--green)" stroke-width="1.5"><path d="M17 2l13 5v9c0 9-6 14-13 17C10 30 4 25 4 16V7z"/><path d="M11 18l4 4 8-9"/></svg><h3>Secure &amp; Safe</h3><p>Your payment is securely processed through Paywell.</p></div>
    <div class="why"><svg width="34" height="36" viewBox="0 0 34 36" fill="none" stroke="var(--green)" stroke-width="1.5"><rect x="3" y="6" width="28" height="26" rx="2"/><path d="M3 13h28M10 3v6M24 3v6"/><path d="M9 18h3M15 18h3M21 18h3M9 23h3M15 23h3M21 23h3M9 28h3M15 28h3"/></svg><h3>Real-Time<br>Availability</h3><p>Up-to-date calendar synced with Staynest and Hoplo.</p></div>
    <div class="why"><svg width="34" height="36" viewBox="0 0 34 36" fill="none" stroke="var(--green)" stroke-width="1.5"><path d="M4 4h13l14 14-13 13L4 17z"/><circle cx="11" cy="11" r="2.5"/></svg><h3>Transparent<br>Pricing</h3><p>No hidden fees.<br>See total price<br>before you book.</p></div>
    <div class="why"><svg width="38" height="36" viewBox="0 0 38 36" fill="none" stroke="var(--green)" stroke-width="1.5"><circle cx="25" cy="9" r="5"/><path d="M15 30c0-7 4-11 10-11s10 4 10 11"/><circle cx="10" cy="15" r="4"/><path d="M2 32c0-6 3-9 8-9"/></svg><h3>Book with<br>Confidence</h3><p>Direct communication with your host from booking to checkout.</p></div>
  </div>
</section>
<aside class="avail-card abs">
  <div class="avail-head">
    <svg width="28" height="28" viewBox="0 0 28 28" fill="none" stroke="#fff" stroke-width="1.6"><rect x="2" y="5" width="24" height="21" rx="2"/><path d="M2 11h24M8 2v5M20 2v5M7 15h3M12.5 15h3M18 15h3M7 20h3M12.5 20h3M18 20h3"/></svg>
    <h3>Ready to Check<br>Availability?</h3>
  </div>
  <p>Select your dates and book your Bend getaway in just a few steps.</p>
  <a class="btn btn-white" href="#">CHECK AVAILABILITY</a>
</aside>

<section class="reviews-head abs">
  <div class="eyebrow">GUEST LOVE</div>
  <h2 class="section-title">Don’t Just Take Our Word For It</h2>
</section>
<article class="review abs" style="left:66px">
  <div class="stars">★★★★★</div>
  <p>“The perfect location! We walked to the Tannery Row Quarter every day. The house was spotless, comfortable and the backyard was amazing for our dog.”</p>
  <div class="who">— Nora P.</div>
</article>
<article class="review abs" style="left:348px">
  <div class="stars">★★★★★</div>
  <p>“One of the best Staynest stays we’ve ever had. Super clean, beautifully decorated and had everything we needed. We’ll definitely be back!”</p>
  <div class="who">— Daniel W.</div>
</article>
<article class="review abs" style="left:629px">
  <div class="stars">★★★★★</div>
  <p>“5-star experience from start to finish. Great communication, easy check-in and the home is even better in person.”</p>
  <div class="who">— Claire M.</div>
</article>
<div class="rating abs">
  <div class="score">4.98</div>
  <div class="lbl">Average Rating</div>
  <ul><li>200+ Reviews</li><li>Staynest Visitor Pick</li><li>Top 1% of Eligible Homes</li></ul>
</div>
<a class="btn reviews-btn abs" href="#">READ MORE REVIEWS</a>

<section class="cta abs" role="img" aria-label="Dusk view of river, footbridge and town lights below a snowy mountain"></section>
<div class="cta-copy abs">
  <div class="eyebrow">YOUR BEND GETAWAY STARTS HERE</div>
  <h2>Book Direct &amp; Start<br>Making Memories</h2>
  <div class="cta-actions">
    <a class="btn" href="#">CHECK AVAILABILITY</a>
    <a class="btn btn-outline" href="#">BOOK DIRECT</a>
  </div>
</div>

<footer class="site-footer abs">
  <div class="foot-brand abs">
    <span class="brand-mark"></span>
    <div>
      <div class="brand-name">BIRCH LANTERN<br>RETREAT</div>
      <div class="brand-sub">BEND, OREGON</div>
    </div>
  </div>
  <div class="foot-col abs" style="left:398px">
    <h4>QUICK LINKS</h4>
    <div class="foot-links">
      <div><a href="#">Home</a><a href="#">The House</a><a href="#">Gallery</a></div>
      <div><a href="#">Explore Bend</a><a href="#">Reviews</a><a href="#">Book Direct</a></div>
      <div style="padding-top:14px"><a href="#">Contact / FAQ</a></div>
    </div>
  </div>
  <div class="foot-col foot-contact abs" style="left:696px">
    <h4>CONNECT</h4>
    <div><svg width="8" height="8" viewBox="0 0 10 10"><path d="M2 1l2 2-1 1.5a6 6 0 002.5 2.5L7 6l2 2-1.5 1.5C4 9 1 6 .5 2.5z" fill="var(--gold)"/></svg>(541) 555-0182</div>
    <div><svg width="8" height="8" viewBox="0 0 10 10"><rect x=".5" y="2" width="9" height="6" fill="none" stroke="var(--gold)"/><path d="M.5 2l4.5 3 4.5-3" fill="none" stroke="var(--gold)"/></svg>stay@birchlantern-example.com</div>
    <div><svg width="8" height="8" viewBox="0 0 10 10"><path d="M5 10S1 6 1 4a4 4 0 018 0c0 2-4 6-4 6z" fill="var(--gold)"/></svg>Bend, Oregon</div>
  </div>
  <div class="foot-col abs" style="left:902px">
    <h4>FOLLOW</h4>
    <div class="socials"><span></span><span></span><span></span></div>
  </div>
  <div class="foot-bottom abs" style="left:241px">© 2024 Birch Lantern Retreat, Bend Oregon. All rights reserved.</div>
  <div class="foot-bottom abs" style="left:702px">Privacy Policy &nbsp;&nbsp;&nbsp;&nbsp;|&nbsp;&nbsp;&nbsp;&nbsp; Terms &amp; Conditions</div>
</footer>

</body>
</html>
```